Landscape design build company door flyer

I would like this flyer to convey a high-level of professionalism for a company that is excellent with communication with their clients as well as a company that does incredible installations

Went on vacation/holiday

```html
<!DOCTYPE html>
<html lang="en">
<head>
<meta charset="UTF-8">
<title>Serene Stone Builders – Door Flyer</title>
<link rel="stylesheet" href="https://fonts.googleapis.com/css2?family=Open+Sans:wght@400;600;700&display=swap">
<style>
  :root {
    --navy: #0f3444;
    --gold: #f9c80e;
    --white: #ffffff;
    --backdrop: #e4e5e7;
    --ink: #0f3444;
  }
  * { box-sizing: border-box; margin: 0; padding: 0; }
  html, body {
    width: 1200px; height: 1082px; overflow: hidden;
    background: var(--backdrop);
    font-family: "Open Sans", Arial, sans-serif;
  }
  .flyer {
    position: absolute; left: 20px; top: 112px;
    width: 1160px; height: 857px;
    background: var(--white);
    display: flex; flex-direction: column;
  }
  .brand-header {
    height: 125px;
    display: flex; align-items: center; justify-content: center; gap: 16px;
  }
  .brand-mark { width: 22px; height: 22px; background: var(--navy); }
  .brand-block { display: flex; flex-direction: column; align-items: center; }
  .brand-name {
    font-weight: 700; font-size: 40px; color: var(--navy);
    letter-spacing: 1px; line-height: 1.05; text-transform: uppercase;
  }
  .brand-tagline {
    font-weight: 700; font-size: 19px; color: var(--navy);
    text-transform: uppercase; letter-spacing: 0.5px;
  }
  .hero-band {
    height: 88px; background: var(--navy);
    display: flex; flex-direction: column; align-items: center; justify-content: center;
    color: var(--gold);
  }
  .hero-title { font-weight: 700; font-size: 40px; line-height: 1.1; }
  .hero-sub { font-weight: 600; font-size: 20px; line-height: 1.3; }
  .gallery {
    height: 421px; background: var(--gold);
    display: grid; grid-template-columns: 282px 275px 275px 283px;
    column-gap: 15px;
  }
  .photo { height: 100%; }
  .photo-pavilion { background: linear-gradient(170deg, #8a5a34 0%, #5e5a56 45%, #3d4045 100%); }
  .photo-pool { background: linear-gradient(180deg, #e9eef2 0%, #c7b9a6 40%, #5fb7b4 75%, #3f8f8c 100%); }
  .photo-firepit { background: linear-gradient(180deg, #4a6fa5 0%, #8a7a6a 40%, #6e5a48 75%, #4b3d33 100%); }
  .photo-path { background: linear-gradient(170deg, #6e5a44 0%, #9a948c 45%, #2d2b2a 100%); }
  .service-area {
    height: 81px;
    display: flex; flex-direction: column; align-items: center; justify-content: center;
    color: var(--ink);
  }
  .service-title { font-weight: 700; font-size: 29px; line-height: 1.2; }
  .service-detail { font-weight: 600; font-size: 13.5px; margin-top: 4px; }
  .feature-band {
    height: 82px; background: var(--navy); color: var(--white);
    display: flex; flex-direction: column; align-items: center; justify-content: center;
  }
  .feature-title { font-weight: 600; font-size: 29px; line-height: 1.2; }
  .feature-sub { font-weight: 600; font-size: 13.5px; margin-top: 4px; }
  .contact-bar {
    flex: 1;
    display: flex; align-items: center; justify-content: space-around;
    padding: 0 30px; color: var(--ink);
    font-size: 22px;
  }
  .contact-item { display: flex; align-items: center; gap: 12px; }
  .contact-icon { width: 27px; height: 27px; flex: none; }
</style>
</head>
<body>
  <main class="flyer">
    <header class="brand-header">
      <span class="brand-mark"></span>
      <div class="brand-block">
        <span class="brand-name">Serene Stone Builders</span>
        <span class="brand-tagline">Outdoor Living Spaces</span>
      </div>
    </header>

    <section class="hero-band">
      <h1 class="hero-title">It’s Time to Discover Your Zen</h1>
      <p class="hero-sub">From vision to reality, let us bring your dream outdoor space to life.</p>
    </section>

    <section class="gallery">
      <div class="photo photo-pavilion" role="img" aria-label="Covered timber pavilion with stacked stone fireplace and outdoor kitchen"></div>
      <div class="photo photo-pool" role="img" aria-label="Modern home terrace beside a turquoise lap pool"></div>
      <div class="photo photo-firepit" role="img" aria-label="Round stone fire pit with terraced retaining walls and plantings at dusk"></div>
      <div class="photo photo-path" role="img" aria-label="Lit stepping stone path over black river rock"></div>
    </section>

    <section class="service-area">
      <h2 class="service-title">Proudly Serving Clients in and around Seattle Since 2018</h2>
      <p class="service-detail">Headquartered in Sammamish, we typically consider projects in Eastside Seattle, including the areas of Bellevue, Issaquah, Kirkland, Redmond, and Sammamish</p>
    </section>

    <section class="feature-band">
      <h2 class="feature-title">Eastside Seattle Outdoor Lighting</h2>
      <p class="feature-sub">Enhance Safety, Beauty, and Ambiance with Custom Outdoor Lighting</p>
    </section>

    <footer class="contact-bar">
      <div class="contact-item">
        <svg class="contact-icon" viewBox="0 0 24 24" aria-hidden="true">
          <circle cx="12" cy="12" r="12" fill="#0f3444"/>
          <path d="M12 5a4.5 4.5 0 0 0-4.5 4.5c0 3.3 4.5 8.5 4.5 8.5s4.5-5.2 4.5-8.5A4.5 4.5 0 0 0 12 5z" fill="#fff"/>
          <circle cx="12" cy="9.5" r="1.7" fill="#0f3444"/>
        </svg>
        <span>4820 Cedar Hollow Ln, Sammamish, WA 98074</span>
      </div>
      <div class="contact-item">
        <svg class="contact-icon" viewBox="0 0 24 24" aria-hidden="true">
          <circle cx="12" cy="12" r="12" fill="#0f3444"/>
          <path d="M8.2 6.5l1.8-.4 1.3 3-1.2 1a7.5 7.5 0 0 0 3.8 3.8l1-1.2 3 1.3-.4 1.8c-.2.6-.8 1-1.4.9A10 10 0 0 1 7.3 7.9c0-.6.3-1.2.9-1.4z" fill="#fff"/>
        </svg>
        <span>(206) 555-0148</span>
      </div>
      <div class="contact-item">
        <svg class="contact-icon" viewBox="0 0 24 24" aria-hidden="true">
          <circle cx="12" cy="12" r="12" fill="#0f3444"/>
          <rect x="6" y="8" width="12" height="8.5" rx="0.8" fill="none" stroke="#fff" stroke-width="1.4"/>
          <path d="M6.3 8.4L12 13l5.7-4.6M6.5 16l4-3.6M17.5 16l-4-3.6" fill="none" stroke="#fff" stroke-width="1.2"/>
        </svg>
        <span>info@serenestonebuilders.com</span>
      </div>
    </footer>
  </main>
</body>
</html>
```